Hip surgeon needs a educative book cover design

I need to re-design my old book cover for its 3rd edition.
It's a small book dedicated to my patients, who underwent total hip replacement. It's meant to help people getting around the basic care after a total hip replacement surgery and getting back to their normal, active life.
The title is: "Morning light rituals: a quiet companion".
I already had a new logo, new stationery and new website design from ArtFolio (please see the attachments).
The final design should be look alike the other fresh new designs. It must communicate health, peacefulness.
I also attached the manual as it looks today for reference.
A5 size.
Just cover and back cover.
Health

```html
<!DOCTYPE html>
<html lang="en">
<head>
<meta charset="utf-8">
<title>Morning Light Rituals – Book Cover</title>
<link rel="stylesheet" href="https://fonts.googleapis.com/css2?family=Montserrat:wght@500;800&family=Open+Sans:wght@400;600&display=swap">
<style>
  :root {
    --stage-light: #a9a9a9;
    --stage-dark: #4a4a4a;
    --paper: #ffffff;
    --title-blue: #3d7fc6;
    --accent-cyan: #16a3dc;
    --band-top: #2b69b8;
    --band-bottom: #1a4f9c;
    --figure-light: #2c8fd8;
    --figure-dark: #1c63b4;
    --logo-ink: #ffffff;
  }
  * { box-sizing: border-box; margin: 0; padding: 0; }
  html, body {
    width: 1200px;
    height: 749px;
    overflow: hidden;
  }
  body {
    background: radial-gradient(ellipse at 55% 35%, var(--stage-light) 0%, #7d7d7d 55%, var(--stage-dark) 100%);
    font-family: "Open Sans", sans-serif;
    position: relative;
  }
  .cover {
    position: absolute;
    left: 373px;
    top: 54px;
    width: 453px;
    height: 641px;
    background: var(--paper);
    overflow: hidden;
    box-shadow: 0 18px 40px rgba(0,0,0,0.35);
  }
  .cover-band {
    position: absolute;
    left: 0;
    right: 0;
    top: 350px;
    bottom: 0;
    background: linear-gradient(180deg, var(--band-top) 0%, var(--band-bottom) 100%);
  }
  .edition-tab {
    position: absolute;
    left: 0;
    top: 92px;
    width: 118px;
    height: 24px;
    background: var(--accent-cyan);
    color: var(--paper);
    font-family: "Montserrat", sans-serif;
    font-weight: 500;
    font-size: 13px;
    line-height: 24px;
    text-align: right;
    padding-right: 12px;
  }
  .title-block {
    position: absolute;
    left: 128px;
    right: 24px;
    top: 76px;
  }
  .book-title {
    font-family: "Montserrat", sans-serif;
    font-weight: 800;
    font-size: 36px;
    line-height: 1.02;
    color: var(--title-blue);
    letter-spacing: 0.5px;
    text-transform: uppercase;
  }
  .book-title .line-two { display: block; margin-left: -40px; }
  .book-subtitle {
    margin-top: 4px;
    font-family: "Montserrat", sans-serif;
    font-weight: 500;
    font-size: 19px;
    color: var(--accent-cyan);
    padding-left: 64px;
  }
  .cover-illustration {
    position: absolute;
    left: 120px;
    top: 220px;
    width: 230px;
    height: 250px;
    border-radius: 6px;
    background: linear-gradient(180deg, var(--figure-light) 0%, var(--figure-dark) 58%, rgba(28,99,180,0.25) 100%);
  }
  .author-mark {
    position: absolute;
    left: 34px;
    bottom: 40px;
    display: flex;
    align-items: center;
    gap: 10px;
  }
  .author-dot {
    width: 30px;
    height: 30px;
    border-radius: 50%;
    background: var(--logo-ink);
  }
  .author-name {
    font-family: "Open Sans", sans-serif;
    font-weight: 600;
    font-size: 19px;
    color: var(--logo-ink);
  }
</style>
</head>
<body>
  <main class="cover" aria-label="Book cover">
    <div class="cover-band"></div>
    <div class="edition-tab">3rd Edition</div>
    <header class="title-block">
      <h1 class="book-title">Morning Light<span class="line-two">Rituals</span></h1>
      <p class="book-subtitle">A Quiet Companion</p>
    </header>
    <div class="cover-illustration" role="img" aria-label="Blue silhouette of two people walking hand in hand, one with a cane, reflected on the floor"></div>
    <footer class="author-mark">
      <span class="author-dot"></span>
      <span class="author-name">Dr. Lucas M. Ferreira</span>
    </footer>
  </main>
</body>
</html>
```